Fire Risk Assessment App needs a sleek UI design

I need a sleek, modern but professional design for my 5 page Fire Risk Assessment App. Include gradient background, fire themed colours including reds, yellows, light orange and a touch of black. Design must ooze simplicity and professionalism. This is for the UK market. See attached images and word doc for more information.

Target Market(s)

General public and business owners

Industry/Entity Type

Technology / Fire Safety

Colors
00AB8E
00BBA5
67D7C9
C6EFE9
E9F9F6
59FF00
82FF00
B8FF75
E3FFCB
F4FFEA
FFC000
F8CF3A
FAE287
FDF2CF
FEFAEE
F0912C
F2A743
F7CA91
FBE8D2
FDF5EE
EE7325
F08F49
F5BC92
FAE3D3
FDF4ED
EB3D1F
EC4F4E
F09395
F8D3D4
FCEDEE

```html
<!DOCTYPE html>
<html lang="en">
<head>
<meta charset="utf-8">
<title>Fire Risk Assessment App – UI Screens</title>
<link href="https://fonts.googleapis.com/css2?family=Poppins:wght@400;500;600;700&display=swap" rel="stylesheet">
<style>
:root{
  --stage:#878382;
  --black:#150b0d;
  --deep-red:#7e0c18;
  --red:#ec1c24;
  --red-dark:#d5141c;
  --orange:#f7861a;
  --orange-deep:#f26a1b;
  --ink:#2a2a2a;
  --white:#ffffff;
  --yellow:#ffc000;
  --green:#59c91a;
}
*{box-sizing:border-box;margin:0;padding:0}
html,body{width:1200px;height:1027px;overflow:hidden}
body{background:var(--stage);font-family:"Poppins",sans-serif;color:var(--ink);position:relative}
.screen{position:absolute;top:112px;width:331px;overflow:hidden;
  background:linear-gradient(180deg,var(--black) 0%,var(--deep-red) 14%,var(--red) 48%,var(--orange-deep) 80%,var(--orange) 100%)}
.screen--welcome{left:104px;height:786px}
.screen--dashboard{left:448px;height:793px}
.screen--support{left:792px;height:567px;
  background:linear-gradient(180deg,var(--black) 0%,var(--deep-red) 20%,var(--red) 50%,var(--orange-deep) 80%,var(--orange) 100%)}
.sheet{position:absolute;left:25px;top:38px;width:282px;border-radius:14px;
  background:linear-gradient(180deg,rgba(255,255,255,.78) 0%,rgba(255,235,235,.8) 45%,rgba(255,232,212,.9) 100%)}
.abs{position:absolute}
.pill{position:absolute;border-radius:30px;display:flex;align-items:center;font-weight:600;font-size:12.5px;letter-spacing:.1px}
.pill--red{background:var(--red);color:var(--white)}
.pill--orange{background:var(--orange);color:var(--white)}
.pill--outline{background:var(--white);color:var(--red);border:1px solid #e8a0a0}
.circle{position:absolute;border-radius:50%;display:flex;align-items:center;justify-content:center}

/* welcome */
.headline{left:0;width:331px;top:68px;text-align:center;font-weight:700;font-size:20.5px;line-height:21px;color:var(--ink);letter-spacing:-.2px}
.headline em{font-style:normal;color:var(--red)}
.ghost-card{position:absolute;background:rgba(255,255,255,.35);border-radius:6px}
.q-card{left:72px;top:166px;width:188px;height:338px;background:var(--white);border-radius:4px;box-shadow:0 2px 10px rgba(0,0,0,.08)}
.q-card .title{left:26px;top:20px;font-weight:600;font-size:11px;line-height:15px;color:#222}
.q-card .section{left:26px;top:53px;font-weight:600;font-size:11.5px;color:var(--red)}
.q-card .topic{left:26px;top:76px;font-weight:500;font-size:7.3px;color:#222}
.q-card .qnum{left:26px;top:109px;font-weight:500;font-size:13px}
.q-card .question{left:27px;top:135px;width:150px;font-size:9.8px;line-height:13px;color:#444}
.answer-row{left:24px;top:191px;display:flex;gap:9px}
.answer-row span{width:21px;height:21px;border:1px solid #333;border-radius:50%;display:flex;align-items:center;justify-content:center}
.q-card .field{left:14px;top:230px;width:160px;height:33px;border:1px solid #555;border-radius:20px;font-size:7.5px;color:#555;display:flex;align-items:center;padding-left:20px}
.q-card .photo{left:64px;top:274px;width:61px;height:48px;border-radius:8px;background:radial-gradient(circle at 50% 55%,#ffb347 0%,#e0561d 40%,#5b3b34 100%)}
.tagline{left:54px;top:518px;font-weight:600;font-size:14.5px;line-height:19px;color:#333}
.credit{left:53px;top:691px;font-weight:600;font-size:12.5px;line-height:17px;color:#222}
.credit span{display:block;padding-left:3px}
.round-ctrl{width:37px;height:37px;border:1.5px solid #222;background:var(--white)}

/* dashboard */
.title-lg{font-weight:700;font-size:20px;color:#2b2b2b;letter-spacing:.2px}
.list-item{position:absolute;left:59px;display:flex;align-items:center;gap:7px;font-weight:600;font-size:12.6px;color:#1f1f1f}
.radio{width:19px;height:19px;border:1.5px solid #888;border-radius:50%;background:var(--white);flex:none}
.divider{position:absolute;left:0;width:100%;height:1px;background:rgba(255,255,255,.3)}
.nav-icon{background:var(--white);border:1px solid rgba(0,0,0,.06)}
.icon-art{border-radius:50%}

/* support */
.support-title{left:89px;top:64px;font-weight:700;font-size:20px;color:var(--white);letter-spacing:.1px}
.hint{left:46px;top:119px;font-size:11px;color:#3a2a2a}
.textarea{left:42px;top:146px;width:246px;height:221px;background:var(--white);border:1px solid #ccc;border-radius:2px}
</style>
</head>
<body>

<svg width="0" height="0" style="position:absolute">
  <defs>
    <symbol id="gauge" viewBox="0 0 40 40">
      <circle cx="20" cy="20" r="18" fill="#fff" stroke="#ccc" stroke-width="1.5"/>
      <path d="M7 24 A13 13 0 0 1 14 9" fill="none" stroke="#ec1c24" stroke-width="3"/>
      <path d="M14 9 A13 13 0 0 1 26 9" fill="none" stroke="#59c91a" stroke-width="3"/>
      <path d="M26 9 A13 13 0 0 1 33 24" fill="none" stroke="#ec1c24" stroke-width="3"/>
      <line x1="20" y1="26" x2="14" y2="15" stroke="#222" stroke-width="1.6"/>
      <circle cx="21" cy="27" r="3" fill="#222"/>
    </symbol>
    <symbol id="card" viewBox="0 0 40 40">
      <rect x="9" y="10" width="20" height="14" rx="2" transform="rotate(-25 19 17)" fill="#6fa8dc"/>
      <rect x="9" y="16" width="23" height="15" rx="2" fill="#ffc000"/>
      <rect x="9" y="19" width="23" height="3" fill="#8a5a00"/>
      <rect x="12" y="25" width="8" height="2" fill="#fff"/>
    </symbol>
    <symbol id="chat" viewBox="0 0 40 40">
      <circle cx="20" cy="20" r="19" fill="#ffc000"/>
      <path d="M11 12 h18 a2 2 0 0 1 2 2 v9 a2 2 0 0 1 -2 2 h-6 l-4 4 v-4 h-8 a2 2 0 0 1 -2 -2 v-9 a2 2 0 0 1 2 -2z" fill="#fff"/>
      <rect x="14" y="16" width="12" height="2" fill="#ffc000"/>
      <rect x="14" y="20" width="9" height="2" fill="#ffc000"/>
    </symbol>
    <symbol id="mic" viewBox="0 0 20 20">
      <rect x="7.5" y="3" width="5" height="9" rx="2.5" fill="#222"/>
      <path d="M5 10 a5 5 0 0 0 10 0 M10 15 v2" fill="none" stroke="#222" stroke-width="1.4"/>
    </symbol>
  </defs>
</svg>

<!-- Screen 1: welcome -->
<section class="screen screen--welcome">
  <div class="sheet" style="height:743px"></div>
  <h1 class="abs headline">THE MOST USER FRIENDLY<br><em>FIRE RISK ASSESSMENT</em><br>APP AVAILABLE.</h1>

  <div class="ghost-card" style="left:110px;top:212px;width:190px;height:330px;transform:rotate(12deg)"></div>
  <div class="ghost-card" style="left:95px;top:200px;width:190px;height:330px;transform:rotate(6deg)"></div>
  <div class="ghost-card" style="left:62px;top:190px;width:190px;height:330px;transform:rotate(-6deg)"></div>

  <article class="abs q-card">
    <p class="abs title">FIRE RISK ASSESSMENT<br>FIRE HAZARDS</p>
    <p class="abs section">Section 7.00/30.00</p>
    <p class="abs topic">ELECTRONIC SOURCES OF IGNITION</p>
    <p class="abs qnum">Q:7:01</p>
    <div class="circle" style="left:81px;top:94px;width:26px;height:26px;background:var(--red)">
      <svg width="12" height="14" viewBox="0 0 12 14"><path d="M7 0 L1 8 h4 l-1 6 l6 -8 h-4z" fill="#fff"/></svg>
    </div>
    <p class="abs question">Are reasonable measures taken &amp; prevent fires of electrical origin?</p>
    <div class="abs answer-row">
      <span><svg width="11" height="11" viewBox="0 0 11 11"><path d="M1.5 5.5 l3 3 l5 -6" fill="none" stroke="#222" stroke-width="1.6"/></svg></span>
      <span><svg width="9" height="9" viewBox="0 0 9 9"><path d="M1 1 l7 7 M8 1 l-7 7" stroke="#222" stroke-width="1.6"/></svg></span>
      <span><svg width="9" height="3" viewBox="0 0 9 3"><rect width="9" height="2" fill="#222"/></svg></span>
      <span><svg width="13" height="9" viewBox="0 0 13 9"><path d="M3 9 a3 3 0 0 1 0 -6 a4 4 0 0 1 7 1 a2.5 2.5 0 0 1 0 5z" fill="#222"/></svg></span>
      <span><svg width="13" height="13"><use href="#mic"/></svg></span>
    </div>
    <div class="abs field">loremipsumdeerqjwjsa</div>
    <div class="abs photo" role="img" aria-label="Photo of a building fire with a firefighter"></div>
  </article>

  <p class="abs tagline">Quick tap responses and<br>voice activated typing</p>

  <div class="pill pill--red" style="left:46px;top:574px;width:240px;height:44px;padding-left:24px;gap:10px">
    <svg width="28" height="28" viewBox="0 0 28 28"><circle cx="14" cy="14" r="13" fill="none" stroke="#fff" stroke-width="1.3"/><circle cx="12" cy="11" r="3.5" fill="none" stroke="#fff" stroke-width="1.3"/><path d="M6 20 a6 5 0 0 1 12 0" fill="none" stroke="#fff" stroke-width="1.3"/><circle cx="20" cy="15" r="3" fill="none" stroke="#fff" stroke-width="1.2"/><path d="M20 13.5 v3 M18.5 15 h3" stroke="#fff" stroke-width="1.1"/></svg>
    CREATE A FREE ACCOUNT
  </div>
  <div class="pill pill--orange" style="left:46px;top:628px;width:240px;height:44px;padding-left:24px;gap:10px">
    <svg width="28" height="28" viewBox="0 0 28 28"><circle cx="13" cy="13" r="12" fill="none" stroke="#fff" stroke-width="1.3"/><circle cx="13" cy="11" r="4" fill="none" stroke="#fff" stroke-width="1.3"/><path d="M5 22 a8 6 0 0 1 12 -3" fill="none" stroke="#fff" stroke-width="1.3"/><rect x="18" y="19" width="7" height="6" rx="1" fill="none" stroke="#fff" stroke-width="1.2"/><path d="M19.5 19 v-2 a2 2 0 0 1 4 0 v2" fill="none" stroke="#fff" stroke-width="1.2"/></svg>
    CUSTOMER LOGIN
  </div>

  <p class="abs credit">Created and endorsed by Northgate<span>Safety</span></p>

  <div class="circle round-ctrl" style="left:180px;top:807px;transform:translate(-50%,-50%);left:179px;top:750px">
    <svg width="22" height="22" viewBox="0 0 22 22" fill="none" stroke="#222" stroke-width="1.2"><path d="M4 8 a8 8 0 0 1 14 0"/><path d="M5 14 v-3 a6 6 0 0 1 12 0 v4"/><path d="M8 18 v-7 a3 3 0 0 1 6 0 v6"/><path d="M11 11 v8"/></svg>
  </div>
  <div class="circle round-ctrl" style="left:236px;top:750px;transform:translate(-50%,-50%)">
    <svg width="22" height="22"><use href="#mic"/></svg>
  </div>
</section>

<!-- Screen 2: dashboard -->
<section class="screen screen--dashboard">
  <div class="sheet" style="height:670px"></div>
  <div class="circle" style="left:47px;top:57px;width:50px;height:50px;background:#fff;box-shadow:0 1px 4px rgba(0,0,0,.2)">
    <svg width="46" height="46"><use href="#gauge"/></svg>
  </div>
  <h2 class="abs title-lg" style="left:119px;top:69px">DASHBOARD</h2>

  <svg class="abs" style="left:0;top:0" width="331" height="320">
    <path d="M154 202 L144 245 M176 202 L186 246" stroke="#333" stroke-width="1" stroke-dasharray="3 3" fill="none"/>
  </svg>
  <div class="circle" style="left:115px;top:118px;width:101px;height:101px;background:var(--red);box-shadow:0 2px 6px rgba(0,0,0,.2)">
    <svg width="56" height="56" viewBox="0 0 56 56"><rect x="22" y="0" width="12" height="56" rx="2" fill="#fff"/><rect x="0" y="22" width="56" height="12" rx="2" fill="#fff"/></svg>
  </div>
  <div class="circle" style="left:75px;top:237px;width:58px;height:58px;background:#fff;border:2px solid #111">
    <div class="icon-art" role="img" aria-label="Office building illustration" style="width:34px;height:34px;background:linear-gradient(180deg,#c9cdf5,#7b86d9)"></div>
  </div>
  <div class="circle" style="left:188px;top:238px;width:58px;height:58px;background:#fff;border:2px solid #111">
    <div class="icon-art" role="img" aria-label="Commercial building illustration" style="width:34px;height:34px;background:linear-gradient(180deg,#ffd84a,#e0a800)"></div>
  </div>

  <div class="pill pill--red" style="left:39px;top:326px;width:176px;height:44px;padding-left:26px;justify-content:flex-start">
    COMPLETE
    <span class="circle" style="position:static;width:23px;height:23px;background:var(--green);margin-left:27px">
      <svg width="12" height="10" viewBox="0 0 12 10"><path d="M1.5 5 l3 3 l6 -7" fill="none" stroke="#fff" stroke-width="2"/></svg>
    </span>
  </div>
  <div class="circle" style="left:36px;top:384px;width:32px;height:32px;background:#fff">
    <div class="icon-art" role="img" aria-label="Office building illustration" style="width:20px;height:20px;background:linear-gradient(180deg,#c9cdf5,#7b86d9)"></div>
  </div>
  <p class="abs" style="left:75px;top:391px;font-weight:600;font-size:13px;color:#1f1f1f">Reg’s Barbershop</p>

  <div class="pill pill--outline" style="left:39px;top:431px;width:176px;height:44px;padding-left:25px">
    IN PROGRESS
    <svg width="24" height="24" viewBox="0 0 24 24" style="margin-left:19px"><circle cx="12" cy="12" r="10" fill="none" stroke="#e6e6e6" stroke-width="1.6"/><path d="M12 2 a10 10 0 1 1 -9 14" fill="none" stroke="#2aa84a" stroke-width="1.6"/></svg>
  </div>
  <div class="list-item" style="top:491px;left:50px"><span class="radio"></span>Elmfield Road School</div>
  <div class="list-item" style="top:517px;left:50px"><span class="radio"></span>Oakmere Nursing Home</div>

  <div class="pill pill--outline" style="left:39px;top:551px;width:176px;height:44px;padding-left:25px">
    PURCHASES
    <span class="circle" style="position:static;width:24px;height:24px;background:#fbe4b8;margin-left:20px">
      <svg width="12" height="13" viewBox="0 0 12 13"><rect x="1" y="4" width="10" height="8" rx="1" fill="none" stroke="#ec1c24" stroke-width="1.2"/><path d="M4 4 v-1 a2 2 0 0 1 4 0 v1" fill="none" stroke="#ec1c24" stroke-width="1.2"/></svg>
    </span>
  </div>
  <div class="list-item" style="top:610px;left:50px"><span class="radio"></span>Residential fire risk assessment</div>
  <div class="list-item" style="top:636px;left:50px"><span class="radio"></span>Commercial fire risk assessment</div>
  <div class="list-item" style="top:661px;left:50px"><span class="radio"></span>Commercial fire risk assessment</div>

  <div class="divider" style="top:716px"></div>
  <nav>
    <div class="circle nav-icon" style="left:25px;top:720px;width:64px;height:64px"><svg width="56" height="56"><use href="#gauge"/></svg></div>
    <div class="circle nav-icon" style="left:107px;top:729px;width:46px;height:46px"><svg width="34" height="34"><use href="#card"/></svg></div>
    <div class="circle nav-icon" style="left:179px;top:729px;width:46px;height:46px"><svg width="32" height="32"><use href="#chat"/></svg></div>
    <div class="circle nav-icon" style="left:251px;top:729px;width:46px;height:46px"><div class="icon-art" role="img" aria-label="Fire exit sign illustration" style="width:28px;height:28px;background:linear-gradient(180deg,#f49a9a,#d9363d)"></div></div>
  </nav>
</section>

<!-- Screen 3: technical support -->
<section class="screen screen--support">
  <div class="sheet" style="height:436px;background:linear-gradient(180deg,rgba(255,255,255,.65) 0%,rgba(255,200,205,.45) 45%,rgba(255,220,200,.55) 100%)"></div>
  <div class="circle" style="left:36px;top:56px;width:45px;height:45px;background:#fff"><svg width="34" height="34"><use href="#chat"/></svg></div>
  <h2 class="abs support-title">TECHNICAL SUPPORT</h2>
  <p class="abs hint">Type/Record your response here</p>
  <div class="circle" style="left:262px;top:117px;width:21px;height:21px;background:#fff;border:1px solid #333"><svg width="13" height="13"><use href="#mic"/></svg></div>
  <div class="abs textarea"></div>
  <div class="pill pill--red" style="left:194px;top:375px;width:94px;height:43px;justify-content:center;font-size:14px">SEND</div>

  <div class="divider" style="top:470px"></div>
  <nav>
    <div class="circle nav-icon" style="left:34px;top:499px;width:46px;height:46px"><svg width="42" height="42"><use href="#gauge"/></svg></div>
    <div class="circle nav-icon" style="left:107px;top:499px;width:46px;height:46px"><svg width="34" height="34"><use href="#card"/></svg></div>
    <div class="circle nav-icon" style="left:179px;top:499px;width:46px;height:46px"><svg width="32" height="32"><use href="#chat"/></svg></div>
    <div class="circle nav-icon" style="left:243px;top:490px;width:64px;height:64px"><div class="icon-art" role="img" aria-label="Fire exit sign illustration" style="width:34px;height:34px;background:linear-gradient(180deg,#f49a9a,#d9363d)"></div></div>
  </nav>
</section>

</body>
</html>
```